Creative, Colorful, Dynamic Infographic for Global Non-Profit

We are a global arts and education non-profit in need of an infographic that illustrates four key skills embedded in our work: Curiosity, Listening, Imagination, Postive Action.
We work primarily with educators, students, and artists who use the power of personal stories to build community and connection and to bridge divides.
Our new brand guidelines, logos, and fonts are here: https://stylevault.example/lumen-circle
I've attached a mock-up of the graphic and the required text. (Note the attached design was created by a staff person, your final design does not need to be the same. The color scheme and text of the final design should match the brand guidelines above.)
The graphic will be used for both web and print media and should include the purple Lumen Circle logo (also attached).
Ideally the final design will delight audiences and spark interest in our work.

```html
<!DOCTYPE html>
<html lang="en">
<head>
<meta charset="utf-8">
<title>4 Key Skills Embedded in Our Work – Lumen Circle</title>
<link href="https://fonts.googleapis.com/css2?family=Poppins:wght@400;500;600;700;800&family=Cinzel:wght@400;500&display=swap" rel="stylesheet">
<style>
  :root {
    --purple: #65318f;
    --purple-deep: #5a2a82;
    --ink: #1f1d20;
    --icon-bg: #e9e8ec;
    --cream: #f4e6d6;
    --cream-soft: #f6ece2;
    --white: #ffffff;
  }
  * { box-sizing: border-box; margin: 0; padding: 0; }
  html, body { width: 800px; height: 1200px; overflow: hidden; background: var(--white); }
  .poster {
    position: relative;
    width: 800px;
    height: 1200px;
    background: linear-gradient(180deg, var(--cream) 0%, var(--white) 32%, var(--white) 70%, var(--cream-soft) 100%);
    font-family: "Poppins", sans-serif;
    color: var(--ink);
    overflow: hidden;
  }
  .shapes { position: absolute; inset: 0; }

  .headline-number {
    position: absolute; left: 46px; top: 22px;
    font-family: "Poppins", sans-serif; font-weight: 800;
    font-size: 150px; line-height: 1; color: var(--purple);
    letter-spacing: -4px;
  }
  .headline-band {
    position: absolute; left: 128px; top: 88px; width: 268px; height: 58px;
    background: linear-gradient(90deg, #000 0%, #141414 55%, #5a5a5a 100%);
  }
  .headline-label {
    position: absolute; left: 148px; top: 91px;
    font-weight: 700; font-size: 37px; color: var(--white); letter-spacing: 0.5px;
  }
  .headline-side {
    position: absolute; right: 64px; top: 62px; text-align: right;
    font-weight: 700; line-height: 1.05;
  }
  .headline-side .accent { display: block; color: var(--purple); font-size: 38px; letter-spacing: 1px; }
  .headline-side .main { display: block; color: var(--ink); font-size: 38px; }
  .headline-rule {
    position: absolute; left: 618px; top: 160px; width: 118px; height: 4px; background: var(--purple);
  }

  .skill { position: absolute; color: var(--white); }
  .skill-title { font-family: "Cinzel", serif; font-weight: 500; font-size: 23px; letter-spacing: 1px; line-height: 1.2; }
  .skill-text { font-size: 15.5px; line-height: 21px; margin-top: 4px; }
  .skill--right { text-align: right; }
  .skill--curiosity { left: 95px; top: 446px; }
  .skill--imagination { right: 96px; top: 446px; }
  .skill--listening { left: 95px; top: 690px; }
  .skill--action { right: 96px; top: 702px; }

  .link-note {
    position: absolute; font-weight: 500; font-size: 15.5px; line-height: 21px; color: var(--ink);
  }
  .link-note--top { left: 0; width: 804px; top: 302px; text-align: center; }
  .link-note--left { left: 150px; top: 613px; }
  .link-note--right { right: 151px; top: 613px; text-align: right; }
  .link-note--bottom { left: 0; width: 804px; top: 912px; text-align: center; }

  .footer-brand {
    position: absolute; left: 70px; top: 1066px; display: flex; align-items: center; gap: 14px;
  }
  .footer-dot { width: 56px; height: 56px; border-radius: 50%; background: var(--purple); }
  .footer-name { font-weight: 500; font-size: 25px; color: var(--purple); letter-spacing: 1px; }
  .footer-url { position: absolute; right: 60px; top: 1078px; font-weight: 500; font-size: 23px; color: var(--ink); }
</style>
</head>
<body>
<main class="poster">
  <svg class="shapes" width="800" height="1200" viewBox="0 0 800 1200" aria-hidden="false">
    <!-- headline slashes -->
    <g fill="var(--purple)">
      <polygon points="402,86 412,86 396,150 386,150"/>
      <polygon points="418,86 428,86 412,150 402,150"/>
    </g>

    <!-- skill boxes -->
    <g fill="var(--purple)">
      <rect x="66" y="377" width="298" height="197" rx="16"/>
      <rect x="442" y="377" width="299" height="197" rx="16"/>
      <rect x="66" y="680" width="298" height="195" rx="16"/>
      <rect x="442" y="680" width="299" height="195" rx="16"/>
    </g>

    <!-- connectors -->
    <g fill="var(--purple)">
      <polygon points="96,566 134,566 134,638 115,650 96,638"/>
      <polygon points="450,413 412,413 400,433 412,454 450,454"/>
      <polygon points="358,803 418,803 428,825 418,847 358,847"/>
      <polygon points="663,690 663,616 682,604 701,616 701,690"/>
    </g>
    <g fill="none" stroke="var(--purple)" stroke-width="5" stroke-linejoin="miter">
      <polyline points="93,650 115,664 137,650"/>
      <polyline points="398,409 384,433 398,457"/>
      <polyline points="432,801 446,825 432,849"/>
      <polyline points="660,601 682,587 704,601"/>
    </g>

    <!-- icon rings -->
    <g fill="var(--purple)">
      <circle cx="140" cy="352" r="84"/>
      <circle cx="665" cy="352" r="84"/>
      <circle cx="138" cy="880" r="84"/>
      <circle cx="669" cy="880" r="84"/>
      <circle cx="402" cy="626" r="50"/>
    </g>
    <circle cx="140" cy="352" r="72" fill="var(--icon-bg)" role="img" aria-label="Icon area: light bulb with a question mark"/>
    <circle cx="665" cy="352" r="72" fill="var(--icon-bg)" role="img" aria-label="Icon area: head with ideas rising out of it"/>
    <circle cx="138" cy="880" r="72" fill="var(--icon-bg)" role="img" aria-label="Icon area: ear listening to sound"/>
    <circle cx="669" cy="880" r="72" fill="var(--icon-bg)" role="img" aria-label="Icon area: hands clasped together"/>
  </svg>

  <div class="headline-number">4</div>
  <div class="headline-band"></div>
  <div class="headline-label">KEY SKILLS</div>
  <h1 class="headline-side"><span class="accent">EMBEDDED</span><span class="main">IN OUR WORK</span></h1>
  <div class="headline-rule"></div>

  <section class="skill skill--curiosity">
    <h2 class="skill-title">CURIOSITY</h2>
    <p class="skill-text">Focus on how you can learn<br>from another’s knowledge<br>and experience</p>
  </section>
  <section class="skill skill--imagination skill--right">
    <h2 class="skill-title">IMAGINATION</h2>
    <p class="skill-text">Focus on how you can learn<br>from another’s knowledge<br>and experience</p>
  </section>
  <section class="skill skill--listening">
    <h2 class="skill-title">LISTENING</h2>
    <p class="skill-text">Seek to understand<br>before speaking</p>
  </section>
  <section class="skill skill--action skill--right">
    <h2 class="skill-title">POSITIVE ACTION</h2>
    <p class="skill-text">Show your words and<br>actions matter</p>
  </section>

  <p class="link-note link-note--top">Your positive actions lead to<br>curiosity about what else is possible</p>
  <p class="link-note link-note--left">Your curiosity allows<br>you to listen</p>
  <p class="link-note link-note--right">Your imagination can<br>spark positive action</p>
  <p class="link-note link-note--bottom">Your listening allows you to<br>take in new information</p>

  <footer>
    <div class="footer-brand">
      <span class="footer-dot"></span>
      <span class="footer-name">LUMEN CIRCLE</span>
    </div>
    <div class="footer-url">www.lumencircle.example</div>
  </footer>
</main>
</body>
</html>
```